Automotive eCommerce Business looking for a business card design

Looking for a clean and simple business card design. Our company name is "Brindle Auto" and we are a company specializing in the ecommerce sales of automotive parts, specifically for pick up trucks and large SUVs. Our company colours are red, black, and white.

Feel free to use the logo provided or create a new logo that you seem fit. Looking forward to your creative ideas!

Industry/Entity Type

Automotive

Contact Information for Business Card

We were thinking of a possibly two-sided design featuring just the logo and company name on one side, and personal information on the other side. Single sided designs will be considered as well.

Font styles to use
Serif
Sans Serif
Decorative

Colors
ec1f27
ffffff
000000

Requirements
Must have
• Space for employee's name, title, phone number and email address, along with the company address and website somewhere.

```html
<!DOCTYPE html>
<html lang="en">
<head>
<meta charset="utf-8">
<title>Brindle Auto Ltd. – Business Card</title>
<link rel="stylesheet" href="https://fonts.googleapis.com/css2?family=Cinzel:wght@400&family=Roboto:wght@400;500&display=swap">
<style>
  :root {
    --brand-red: #9e1c21;
    --slate: #4b5052;
    --card-white: #ffffff;
    --ink-grey: #555555;
    --backdrop: #e8e5e1;
    --light-text: #f2f2f2;
  }
  * { margin: 0; padding: 0; box-sizing: border-box; }
  html, body { width: 1200px; height: 960px; overflow: hidden; }
  body { background: var(--backdrop); position: relative; font-family: "Roboto", sans-serif; }

  .card {
    position: absolute;
    width: 602px;
    border-radius: 18px;
    overflow: hidden;
    box-shadow: 0 3px 10px rgba(0,0,0,0.25);
  }
  .card-front { left: 320px; top: 100px; height: 345px; background: var(--card-white); }
  .card-back { left: 320px; top: 493px; height: 342px; }
  .card-back .card-shape { position: absolute; inset: 0; }

  .brand-mark {
    position: absolute;
    background: var(--brand-red);
    border-radius: 14px;
  }
  .card-front .brand-mark { left: 228px; top: 74px; width: 150px; height: 150px; }
  .card-back .brand-mark { left: 368px; top: 85px; width: 130px; height: 130px; }

  .brand-name {
    position: absolute;
    font-family: "Cinzel", serif;
    font-weight: 400;
    color: var(--ink-grey);
    white-space: nowrap;
    transform: translateX(-50%);
  }
  .card-front .brand-name { left: 302px; top: 238px; font-size: 25px; }
  .card-back .brand-name { left: 433px; top: 228px; font-size: 21px; }

  .web-address {
    position: absolute;
    left: 302px; top: 298px;
    transform: translateX(-50%);
    font-size: 14px;
    letter-spacing: 5px;
    color: var(--ink-grey);
    white-space: nowrap;
  }

  .person { position: absolute; left: 34px; top: 26px; text-transform: uppercase; }
  .person-name { color: var(--brand-red); font-size: 19px; font-weight: 400; line-height: 24px; }
  .person-title { color: var(--light-text); font-size: 14px; font-weight: 500; line-height: 20px; }

  .address { position: absolute; left: 34px; top: 169px; color: var(--light-text); font-size: 14px; line-height: 18px; }

  .contact-list { position: absolute; left: 34px; top: 216px; list-style: none; }
  .contact-list li {
    display: flex; align-items: center;
    color: var(--light-text); font-size: 14px; line-height: 19px;
  }
  .contact-list svg { width: 12px; height: 12px; margin-right: 11px; fill: var(--brand-red); flex: none; }
</style>
</head>
<body>

<section class="card card-front" aria-label="Card front">
  <div class="brand-mark" aria-hidden="true"></div>
  <p class="brand-name">Brindle Auto Ltd.</p>
  <p class="web-address">www.brindleauto.com</p>
</section>

<section class="card card-back" aria-label="Card back">
  <svg class="card-shape" width="602" height="342" viewBox="0 0 602 342" aria-hidden="true">
    <rect width="602" height="342" fill="var(--slate)"/>
    <path d="M400,0 H602 V342 H424 Q410,342 400,334 L272,262 Q257,254 257,238 V118 Q257,96 272,84 C300,62 330,34 358,16 Q378,0 400,0 Z" fill="var(--card-white)"/>
  </svg>

  <div class="person">
    <p class="person-name">Dana Whitlock</p>
    <p class="person-title">CEO/Founder</p>
  </div>

  <p class="address">2914 Larchwood Lane<br>Fairbanks, Alaska 99701</p>

  <ul class="contact-list">
    <li><svg viewBox="0 0 12 12"><path d="M2.5 0.5 L4.5 0.5 L5.2 3 L3.8 4.3 Q5 7 7.7 8.2 L9 6.8 L11.5 7.5 V9.5 Q11 11.5 9 11.5 Q1 10.5 0.5 3 Q0.5 1 2.5 0.5 Z"/></svg>555 310 2281</li>
    <li><svg viewBox="0 0 12 12"><path d="M3 0 H9 Q10 0 10 1 V11 Q10 12 9 12 H3 Q2 12 2 11 V1 Q2 0 3 0 Z M3.3 1.5 V9.5 H8.7 V1.5 Z"/></svg>555 742 6190</li>
    <li><svg viewBox="0 0 12 12"><path d="M3 1 H9 V4 H3 Z M1 5 H11 Q12 5 12 6 V11 H0 V6 Q0 5 1 5 Z"/></svg>555 408 3375</li>
    <li><svg viewBox="0 0 12 12"><path d="M0 2 H12 V10 H0 Z M0.8 2.8 L6 6.6 L11.2 2.8 V3.6 L6 7.6 L0.8 3.6 Z" fill-rule="evenodd"/></svg>dana@brindleauto.com</li>
    <li><svg viewBox="0 0 12 12"><circle cx="6" cy="6" r="6"/></svg>www.brindleauto.com</li>
  </ul>

  <div class="brand-mark" aria-hidden="true"></div>
  <p class="brand-name">Brindle Auto Ltd.</p>
</section>

</body>
</html>
```